Redesign website for small print company

Vindurgata is a small printing company in Iceland mainly servicing Students, schools, etc. We are also doing all kind of other jobs, like business cards, book printing, brochure printing etc. We are also selling books online.
Our website is: www.vindurgata.is
What we are looking for is:
- Web Design (Uncoded - PSD layout only)
- Mobile friendly design, using our current color scheme: Red, green, yellow and light gray.
- Clean simple design
- Simple, light and easy to use.
- More menu Items/drop down
Industry/Entity Type
Digital Printing
Number of Pages Required
5+ page
Requirements
Must have
- Easy navigation
- Designed for mobile
- Current color scheme (see logo)
Nice to have
- Icon based products

```html
<!DOCTYPE html>
<html lang="en">
<head>
<meta charset="utf-8">
<title>Vindurgata – Printing for students and schools</title>
<link href="https://fonts.googleapis.com/css2?family=Lato:wght@400;700&family=Montserrat:wght@300;400;600;700&display=swap" rel="stylesheet">
<style>
:root{
  --green-deep:#1c3a1d;
  --green-mid:#4f6a1c;
  --olive:#8d9a14;
  --yellow:#f3d40a;
  --yellow-btn:#f7d117;
  --red:#e4382b;
  --white:#ffffff;
  --cream:#f7f2d8;
  --text-green:#1f5e2a;
  --footer-band:#17301a;
  --line:rgba(255,255,255,.55);
}
*{box-sizing:border-box;margin:0;padding:0}
html,body{width:1200px;height:2605px;overflow:hidden}
body{
  position:relative;
  font-family:"Lato",Arial,sans-serif;
  color:var(--white);
  background:linear-gradient(180deg,var(--green-deep) 0%,var(--green-mid) 14%,var(--olive) 32%,var(--yellow) 48%,var(--olive) 62%,var(--green-mid) 76%,var(--green-deep) 90%);
}
.abs{position:absolute}
.brand{font-family:"Lato",sans-serif;font-weight:700;font-size:30px;color:var(--white);letter-spacing:.5px;white-space:nowrap}
.site-header .brand{left:76px;top:36px}
.main-nav{left:439px;top:44px;font-size:19px}
.main-nav a{color:var(--white);text-decoration:none;position:absolute;white-space:nowrap}
.main-nav a.active{color:var(--yellow)}
.cart{left:853px;top:46px}
.social{display:flex;gap:12px}
.social span{width:40px;height:40px;border-radius:50%;background:rgba(255,255,255,.25);border:2px solid rgba(255,255,255,.6);display:block}
.site-header .social{left:920px;top:38px}
.btn{display:inline-flex;align-items:center;justify-content:center;background:var(--yellow-btn);color:#3a2f00;border-radius:30px;font-size:18px;text-transform:uppercase;box-shadow:0 3px 6px rgba(0,0,0,.3);position:absolute}
.hero-title{left:78px;top:188px;font-family:"Montserrat",sans-serif;font-weight:700;font-size:57px;color:var(--red)}
.hero-text{left:79px;top:268px;width:500px;font-size:14px;line-height:25px}
.hero-btn{left:77px;top:398px;width:164px;height:56px}
.hero-photo{left:640px;top:118px;width:400px;height:420px;border-radius:50% 50% 40% 40%;background:radial-gradient(circle at 50% 40%,#2e7a2f 0%,#3a6a22 45%,rgba(70,100,30,0) 72%)}
.section-title{font-family:"Montserrat",sans-serif;font-weight:700;font-size:43px;color:var(--white)}
.fields-title{left:79px;top:596px}
.tabs{left:77px;top:686px;width:1047px;height:46px;border-bottom:1px solid var(--line);font-size:19px}
.tabs span{position:absolute;top:0;white-space:nowrap}
.tabs .active{border-bottom:4px solid var(--white);padding:0 20px 14px;left:0}
.book-photo{left:130px;top:790px;width:315px;height:365px;background:linear-gradient(160deg,#2a2a2a,#111 55%,#6b4b1e);border-radius:6px}
.product-kicker{left:511px;top:782px;font-size:16px;font-weight:700;letter-spacing:.5px}
.product-name{left:511px;top:810px;font-family:"Montserrat",sans-serif;font-weight:400;font-size:31px}
.product-price{left:511px;top:888px;font-size:30px;font-weight:700;color:#13300f}
.stars{left:511px;top:935px}
.product-text{left:511px;top:966px;width:570px;font-size:14px;line-height:25px}
.product-btn{left:509px;top:1084px;width:165px;height:58px}
.slider-arrows{left:1028px;top:780px}
.services-title{left:0;width:1200px;top:1222px;text-align:center;color:var(--text-green)}
.service{width:229px;height:225px;border-radius:22px;background:rgba(255,255,255,.28);padding:14px}
.service-inner{width:100%;height:100%;border-radius:18px;background:rgba(255,255,255,.35);padding:12px}
.service-face{width:100%;height:100%;border-radius:14px;background:var(--cream);display:flex;flex-direction:column;align-items:center;justify-content:center;gap:18px;color:var(--text-green);font-size:21px;box-shadow:0 2px 4px rgba(0,0,0,.15)}
.about-title{left:0;width:1200px;top:1858px;text-align:center}
.about-sub{left:79px;top:1956px;font-family:"Montserrat",sans-serif;font-weight:300;font-size:22px}
.about-text{left:79px;top:2008px;width:480px;font-size:14px;line-height:25px}
.about-btn{left:77px;top:2214px;width:165px;height:56px}
.flyers{left:610px;top:1990px;width:450px;height:260px;transform:rotate(-8deg);border-radius:6px;background:linear-gradient(100deg,#3f7fb8 0%,#e6c23a 30%,#d9562b 50%,#2a3c8a 70%,#e8e4ef 100%)}
.footer-rule{left:77px;top:2334px;width:1047px;border-top:1px solid var(--line)}
.contact-icon{width:52px;height:52px;border-radius:50%;background:var(--white);display:flex;align-items:center;justify-content:center}
.contact-text{font-size:16px;line-height:26px}
.site-footer .brand{left:802px;top:2370px}
.footer-links{left:804px;top:2434px;font-size:14px;white-space:nowrap}
.bottom-band{left:0;top:2522px;width:1200px;height:83px;background:var(--footer-band)}
.copyright{font-size:14px}
.copyright strong{color:var(--yellow);font-weight:700}
.bottom-band .social{position:absolute;left:920px;top:20px}
</style>
</head>
<body>

<header class="site-header">
  <div class="brand abs">VINDURGATA</div>
  <nav class="main-nav abs">
    <a class="active" style="left:0">Home</a>
    <a style="left:84px">Services</a>
    <a style="left:186px">Job submit</a>
    <a style="left:306px">About us</a>
  </nav>
  <svg class="cart abs" width="40" height="24" viewBox="0 0 40 24">
    <path d="M1 3h4l3 11h11l3-8H7" fill="none" stroke="#fff" stroke-width="2"/>
    <circle cx="10" cy="19" r="2" fill="#fff"/><circle cx="18" cy="19" r="2" fill="#fff"/>
    <circle cx="32" cy="8" r="7" fill="#f3d40a"/><text x="32" y="12" font-size="10" text-anchor="middle" fill="#333" font-family="Lato">1</text>
  </svg>
  <div class="social abs" aria-label="Social links"><span></span><span></span><span></span><span></span></div>
</header>

<section class="hero">
  <h1 class="hero-title abs">Vindurgata</h1>
  <p class="hero-text abs">Lorem Ipsum is simply dummy text of the printing and typesetting industry. Lorem Ipsum has been the industry's standard dummy text ever since the 1500s, when an unknown printer took a galley of type and scrambled it to make a type specimen book.</p>
  <a class="btn hero-btn">Learn more</a>
  <div class="hero-photo abs" role="img" aria-label="Smiling student sitting cross-legged beside a stack of books"></div>
</section>

<section class="fields">
  <h2 class="section-title fields-title abs">Fields of use</h2>
  <div class="tabs abs">
    <span class="active">Textbooks</span>
    <span style="left:177px">Posters</span>
    <span style="left:328px">Book Printing</span>
    <span style="left:529px">Lealfeats</span>
    <span style="left:692px">Business Cards</span>
    <span style="left:904px">Essays</span>
  </div>
  <div class="book-photo abs" role="img" aria-label="Stack of printed hardcover books with a dark cover"></div>
  <p class="product-kicker abs">ONLINE BOOK SELLING</p>
  <h3 class="product-name abs">Songs of the Northern Fjords</h3>
  <p class="product-price abs">4.900 kr</p>
  <svg class="stars abs" width="100" height="18" viewBox="0 0 100 18">
    <g fill="#f3d40a" stroke="#7a6a00" stroke-width="1">
      <polygon points="9,1 11,7 17,7 12,11 14,17 9,13 4,17 6,11 1,7 7,7"/>
      <polygon transform="translate(20)" points="9,1 11,7 17,7 12,11 14,17 9,13 4,17 6,11 1,7 7,7"/>
      <polygon transform="translate(40)" points="9,1 11,7 17,7 12,11 14,17 9,13 4,17 6,11 1,7 7,7"/>
      <polygon transform="translate(60)" points="9,1 11,7 17,7 12,11 14,17 9,13 4,17 6,11 1,7 7,7"/>
      <polygon transform="translate(80)" fill="none" points="9,1 11,7 17,7 12,11 14,17 9,13 4,17 6,11 1,7 7,7"/>
    </g>
  </svg>
  <p class="product-text abs">Lorem Ipsum is simply dummy text of the printing and typesetting industry. Lorem Ipsum has been the industry's standard dummy text ever since the 1500s, when an unknown printer took a galley of type and scrambled it to make a type specimen book.</p>
  <a class="btn product-btn">Add to bog</a>
  <svg class="slider-arrows abs" width="96" height="44" viewBox="0 0 96 44">
    <circle cx="21" cy="22" r="20" fill="#fff"/><path d="M24 14l-8 8 8 8" fill="none" stroke="#222" stroke-width="3"/>
    <circle cx="74" cy="22" r="19" fill="none" stroke="#fff" stroke-width="2"/><path d="M71 14l8 8-8 8" fill="none" stroke="#fff" stroke-width="3"/>
  </svg>
</section>

<section class="services">
  <h2 class="section-title services-title abs">Our Services</h2>
  <div class="service abs" style="left:236px;top:1315px"><div class="service-inner"><div class="service-face">
    <svg width="56" height="70" viewBox="0 0 56 70"><rect x="4" y="4" width="48" height="62" rx="3" fill="none" stroke="#111" stroke-width="4"/><circle cx="30" cy="20" r="8" fill="none" stroke="#111" stroke-width="3"/><path d="M12 38h32M12 46h32M12 54h24" stroke="#111" stroke-width="3"/></svg>
    Essays</div></div></div>
  <div class="service abs" style="left:486px;top:1315px"><div class="service-inner"><div class="service-face">
    <svg width="74" height="60" viewBox="0 0 74 60"><rect x="14" y="2" width="56" height="34" fill="#111" transform="rotate(8 42 19)"/><rect x="4" y="18" width="62" height="38" fill="#fff" stroke="#111" stroke-width="4"/><path d="M12 30h30M12 38h40M12 46h24" stroke="#111" stroke-width="3"/></svg>
    Business Cards</div></div></div>
  <div class="service abs" style="left:736px;top:1315px"><div class="service-inner"><div class="service-face">
    <svg width="64" height="70" viewBox="0 0 64 70"><path d="M4 14l26-10v56L4 68z" fill="#111"/><path d="M34 4l26 8v54l-26-6z" fill="#111"/><path d="M40 20l14 4" stroke="#fff" stroke-width="3"/></svg>
    Lealfeats</div></div></div>
  <div class="service abs" style="left:236px;top:1565px"><div class="service-inner"><div class="service-face">
    <svg width="70" height="70" viewBox="0 0 70 70"><rect x="4" y="4" width="62" height="12" fill="#111"/><rect x="4" y="20" width="62" height="26" fill="#111"/><path d="M18 40h34v26H26l-8-8z" fill="#fff" stroke="#111" stroke-width="4"/></svg>
    Book Printing</div></div></div>
  <div class="service abs" style="left:486px;top:1565px"><div class="service-inner"><div class="service-face">
    <svg width="64" height="72" viewBox="0 0 64 72"><path d="M14 4h36l12 66H2z" fill="#111"/><path d="M20 18h24M18 28h28M16 38h32" stroke="#fff" stroke-width="3"/></svg>
    Posters</div></div></div>
  <div class="service abs" style="left:736px;top:1565px"><div class="service-inner"><div class="service-face">
    <svg width="56" height="70" viewBox="0 0 56 70"><rect x="4" y="4" width="48" height="62" rx="3" fill="#111"/><rect x="12" y="12" width="32" height="40" fill="#fff"/><path d="M16 48l10-18 8 12 6-6 4 12z" fill="#111"/></svg>
    Textbooks</div></div></div>
</section>

<section class="about">
  <h2 class="section-title about-title abs">About Vindurgata</h2>
  <p class="about-sub abs">Lorem Ipsum printing and typesetting industry.</p>
  <p class="about-text abs">Lorem ipsum dolor sit amet, consectetur adipiscing elit, sed do eiusmod tempor incididunt ut labore et dolore magna aliqua. Ut enim ad minim veniam, quis nostrud exercitation ullamco laboris nisi ut aliquip ex ea commodo consequat. Duis aute irure dolor in reprehenderit in voluptate velit esse cillum dolore eu fugiat nulla pariatur. Excepteur sint occaecat cupidatat non proident, sunt in culpa qui officia deserunt mollit anim id est laborum.</p>
  <a class="btn about-btn">Add to bog</a>
  <div class="flyers abs" role="img" aria-label="Fan of colourful printed event flyers"></div>
</section>

<footer class="site-footer">
  <div class="footer-rule abs"></div>
  <div class="contact-icon abs" style="left:76px;top:2381px">
    <svg width="24" height="22" viewBox="0 0 24 22"><path d="M12 2L2 11h3v9h5v-6h4v6h5v-9h3z" fill="#e4382b"/></svg>
  </div>
  <p class="contact-text abs" style="left:142px;top:2380px">48 Harbor Lane #12,<br>Eastfield, OR 97401</p>
  <div class="contact-icon abs" style="left:438px;top:2381px">
    <svg width="22" height="22" viewBox="0 0 22 22"><path d="M5 2l4 4-2 3c1 3 3 5 6 6l3-2 4 4-3 3C9 20 2 13 2 5z" fill="#e4382b"/></svg>
  </div>
  <p class="contact-text abs" style="left:505px;top:2380px">+1 555 014 2290<br>info@vindurgata.is</p>
  <div class="brand abs">VINDURGATA</div>
  <p class="footer-links abs">Home &nbsp; | &nbsp; Services &nbsp; | &nbsp; Job Submit &nbsp; | &nbsp; About Us</p>
  <div class="bottom-band abs">
    <p class="copyright abs" style="left:79px;top:33px">Copyright © <strong>Vindurgata</strong> - 2018 . All Right Reserved</p>
    <div class="social" aria-label="Social links"><span></span><span></span><span></span><span></span></div>
  </div>
</footer>

</body>
</html>
```